A new presentation to our clients

we are a Real Estate agency, our website is www.lumibrasa.com and it’s time to have a new, fashion and remarcable Business Card. we want to differentiate ourselves from other companies so we want a business card that differentiates us. we want the business card to impact our customers. in the competitive market that we have today, we have to be different and it is this difference that we seek

Target Market(s)

Real Estate Clients

Contact Information for Business Card

We search a totaly diferent card from the usual

Font styles to use
Sans Serif

Colors
e34197

Requirements
Must have
• Logo, adress, phone contact, e-mail, photo, and our website
Nice to have
• We would like to see a modern business card
Should not have
• Houses or building draws

```html
<!DOCTYPE html>
<html lang="en">
<head>
<meta charset="utf-8">
<title>Lumibrasa Business Card</title>
<link rel="stylesheet" href="https://fonts.googleapis.com/css2?family=Comfortaa:wght@700&family=Nunito:wght@400;600&display=swap">
<style>
  :root {
    --brand-pink: #ec2a7b;
    --ink-dark: #2f2f35;
    --band-dark: #3b3b42;
    --paper: #ffffff;
    --stage: #1f1f22;
    --text-body: #2a2a2e;
  }
  * { box-sizing: border-box; margin: 0; padding: 0; }
  html, body { width: 1200px; height: 877px; overflow: hidden; background: var(--stage); }
  .stage { position: relative; width: 1200px; height: 877px; }

  .card {
    position: absolute;
    left: 280px;
    width: 640px;
    height: 366px;
    border-radius: 3px;
    overflow: hidden;
    box-shadow: 0 14px 30px rgba(0,0,0,0.45);
  }
  .card-front { top: 52px; background: var(--brand-pink); display: flex; align-items: center; justify-content: center; }
  .card-back { top: 458px; background: var(--paper); }

  .brand-name {
    font-family: "Comfortaa", sans-serif;
    font-weight: 700;
    letter-spacing: 1px;
  }
  .card-front .brand-name { color: var(--paper); font-size: 66px; }

  .top-band-dark { position: absolute; left: 0; top: 0; width: 262px; height: 22px; background: var(--band-dark); border-bottom-right-radius: 12px; }
  .top-band-pink { position: absolute; left: 250px; top: 0; right: 0; height: 13px; background: var(--brand-pink); border-bottom-left-radius: 8px; }
  .edge-mark { position: absolute; left: 0; width: 7px; background: var(--band-dark); }
  .edge-mark.one { top: 226px; height: 34px; }
  .edge-mark.two { top: 298px; height: 68px; }

  .card-back .brand-name { position: absolute; left: 40px; top: 84px; color: var(--brand-pink); font-size: 40px; }

  .holder { position: absolute; left: 40px; top: 156px; }
  .holder-name { font-family: "Comfortaa", sans-serif; font-weight: 700; color: var(--brand-pink); font-size: 28px; }
  .holder-role { font-family: "Nunito", sans-serif; font-size: 14px; color: var(--text-body); margin-top: 1px; }

  .contact { position: absolute; left: 40px; top: 232px; font-family: "Nunito", sans-serif; font-size: 13.5px; color: var(--text-body); line-height: 18px; }
  .contact-address { margin-bottom: 4px; }
  .contact-row { display: flex; align-items: center; gap: 7px; }
  .contact-row svg { width: 12px; height: 12px; fill: var(--brand-pink); flex: none; }

  .portrait {
    position: absolute;
    right: 0; top: 34px; bottom: 0;
    width: 300px;
    background: radial-gradient(ellipse at 45% 35%, #c89a82 0%, #8a6452 22%, rgba(60,48,44,0.9) 40%, #2b2b30 70%, #1f1f23 100%);
    -webkit-mask-image: linear-gradient(to right, transparent 0, #000 60px);
            mask-image: linear-gradient(to right, transparent 0, #000 60px);
  }
</style>
</head>
<body>
<main class="stage">
  <section class="card card-front">
    <span class="brand-name">Lumibrasa</span>
  </section>

  <section class="card card-back">
    <div class="top-band-dark"></div>
    <div class="top-band-pink"></div>
    <div class="edge-mark one"></div>
    <div class="edge-mark two"></div>

    <span class="brand-name">Lumibrasa</span>

    <div class="holder">
      <div class="holder-name">Daniel Reyes</div>
      <div class="holder-role">Director</div>
    </div>

    <div class="contact">
      <div class="contact-address">48 Elmwood Lane, Suite B<br>Leeds, UK B0034C</div>
      <div class="contact-row">
        <svg viewBox="0 0 24 24"><path d="M6.6 10.8a15.1 15.1 0 0 0 6.6 6.6l2.2-2.2a1 1 0 0 1 1-.25 11.4 11.4 0 0 0 3.6.57 1 1 0 0 1 1 1V20a1 1 0 0 1-1 1A17 17 0 0 1 3 4a1 1 0 0 1 1-1h3.5a1 1 0 0 1 1 1c0 1.25.2 2.45.57 3.57a1 1 0 0 1-.25 1z"/></svg>
        <span>020 614 3825</span>
      </div>
      <div class="contact-row">
        <svg viewBox="0 0 24 24"><path d="M2 5h20v14H2z M2 5l10 8 10-8" /></svg>
        <span>info@lumibrasa.com</span>
      </div>
      <div class="contact-row">
        <svg viewBox="0 0 24 24"><circle cx="12" cy="12" r="10"/><path d="M2 12h20M12 2c3 3 3 17 0 20M12 2c-3 3-3 17 0 20" stroke="#fff" stroke-width="1.5" fill="none"/></svg>
        <span>www.lumibrasa.com</span>
      </div>
    </div>

    <div class="portrait" role="img" aria-label="Portrait photo of the director in a dark jacket"></div>
  </section>
</main>
</body>
</html>
```